*YO!!! Designers Needed!!* Front Page Cover Needed for a $$Billion Dollar$$ Company

We are a manufacturer of aluminum electrolytic capacitors. We are looking to create a front page cover that will be used on our annual report. We are a publicly listed company and work with many Meridex 400 companies, so your work will be viewed by the BIG GUNS and EXECUTIVES around the WORLD! If selected, you may be selected for additional work.

The front page cover should be unique. If elegance, modern, bling, and creativity somehow got together and had a child, that's what the cover page would look like!

Inspired Examples attached. Check them out!

www.brovanta.com

Font styles to use
Sans Serif

Requirements
Must have
• 1. Must include the attached logo. Logo size, color, and placement are at your discretion.

2. Should include the text, '2020 Annual Report'

3. The design should incorporate the use of foil and/or be embossed. The foil can be part of the design or can be the full page. See various examples attached for reference.

4. Shall be in A4 size and vertical orientation.
Nice to have
• Feel free to add any icons or stock photos (for example capacitors or circuit boards) if needed.

Be creative here and don't be afraid to be bold! The end product will be printed and budget is not a limiting factor, so feel free to make it extravagant if needed.

Our slogan is "Think Ahead". This slogan can or cannot be part of the theme.

```html
<!DOCTYPE html>
<html lang="en">
<head>
<meta charset="utf-8">
<title>Brovanta 2020 Annual Report Cover</title>
<link href="https://fonts.googleapis.com/css2?family=Jost:wght@400;600&display=swap" rel="stylesheet">
<style>
  :root {
    --backdrop: #dcdcdc;
    --cover-black: #000000;
    --foil-silver: #c9c9c9;
    --foil-grey: #8e8e8e;
    --title-white: #ffffff;
  }
  html, body {
    margin: 0;
    padding: 0;
    width: 1200px;
    height: 1000px;
    overflow: hidden;
    background: var(--backdrop);
  }
  .cover {
    position: absolute;
    left: 296px;
    top: 75px;
    width: 608px;
    height: 852px;
    background: var(--cover-black);
    overflow: hidden;
    font-family: "Jost", "Helvetica Neue", Arial, sans-serif;
  }
  .capacitor-art {
    position: absolute;
    left: 0;
    top: 0;
    width: 608px;
    height: 852px;
  }
  .wordmark {
    position: absolute;
    left: 404px;
    top: 415px;
    margin: 0;
    transform-origin: 0 0;
    transform: rotate(-90deg);
    font-size: 68px;
    font-weight: 600;
    line-height: 1;
    letter-spacing: 0.02em;
    color: var(--foil-silver);
    white-space: nowrap;
  }
  .slogan {
    position: absolute;
    left: 532px;
    top: 247px;
    margin: 0;
    transform-origin: 0 0;
    transform: rotate(-90deg);
    font-size: 26px;
    font-weight: 400;
    line-height: 1;
    letter-spacing: 0.04em;
    color: var(--foil-grey);
    white-space: nowrap;
  }
  .report-title {
    position: absolute;
    left: 0;
    right: 0;
    top: 773px;
    margin: 0;
    text-align: center;
    font-size: 15px;
    font-weight: 600;
    letter-spacing: 0.62em;
    color: var(--title-white);
    text-indent: 0.62em;
  }
</style>
</head>
<body>
  <main class="cover">
    <svg class="capacitor-art" viewBox="0 0 608 852" role="img" aria-label="Diagonal line drawing of a capacitor in a blue, purple, yellow and teal gradient">
      <defs>
        <linearGradient id="capacitor-tones" x1="0" y1="800" x2="372" y2="292" gradientUnits="userSpaceOnUse">
          <stop offset="0" stop-color="#3b4fc0"/>
          <stop offset="0.35" stop-color="#a855c8"/>
          <stop offset="0.65" stop-color="#f2e45a"/>
          <stop offset="1" stop-color="#19cfc0"/>
        </linearGradient>
      </defs>
      <polygon points="0,630 372,292 372,395 0,800" fill="url(#capacitor-tones)" opacity="0.55"/>
    </svg>

    <h1 class="wordmark">BROVANTA</h1>
    <p class="slogan">THINK AHEAD.</p>
    <p class="report-title">2020 ANNUAL REPORT</p>
  </main>
</body>
</html>
```